Membership Based Medical Practice Website

We need a functioning website for a new Membership based medical practice. There will be an enrollment fee and a monthly fee. We would like to see designs that are modern, simple. Should use neutral light colors. Examples of sites we like are www.kellanmoorclinic.com and https://fernholtcare.com/ We also have a link that when "Join Now" is clicked it will go to the signup website.

Target Market(s)

Gay Men, local population, Age group 20 to 60's.

Industry/Entity Type

Medical

Coding

Coded - Design and coding required

Number of Pages Required

5+ page

Font styles to use
Sans Serif

Colors
ffffff
cee9f5
ecf7fb
cfeae6
edf8f6
aaaaaa
e9e9e9
dbdbdb
fff3d1

Requirements
Must have
• Logo and header on every page. Clean, simple design, clear content, mobile compatible.
• Must use Wordpress
Nice to have
• Ideas should come from kellanmoorclinic.com
• Easy to read
Should not have
• Generic patient pictures, bold colors.
• Should not copy from above websites.

```html
<!DOCTYPE html>
<html lang="en">
<head>
<meta charset="utf-8">
<title>Larkfield Infectious Disease Specialists</title>
<link rel="stylesheet" href="https://fonts.googleapis.com/css2?family=Montserrat:wght@300;400;500;600;700&display=swap">
<style>
:root{
  --white:#ffffff;
  --teal:#cfeae6;
  --cream:#fff3d1;
  --gold:#f0dc9c;
  --ink:#1f1f1f;
  --text:#555555;
  --line:#e9e9e9;
  --dark:#121212;
}
*{box-sizing:border-box;margin:0;padding:0}
html,body{width:1200px;height:3673px;overflow:hidden}
body{position:relative;background:var(--white);font-family:'Montserrat',sans-serif;color:var(--ink)}
a{text-decoration:none}
.abs{position:absolute}
.center{left:0;width:1200px;text-align:center}

/* header */
.brand{top:18px;left:0;width:1200px;text-align:center}
.brand-mark{width:46px;height:46px;border-radius:50%;border:3px solid var(--gold);margin:0 auto 10px}
.brand-name{font-size:15px;letter-spacing:12px;color:#444;font-weight:400}
.brand-tag{font-size:11px;letter-spacing:1px;color:#666;margin-top:4px}
.main-nav{top:130px;left:0;width:1200px;height:39px;background:var(--teal)}
.main-nav a{position:absolute;top:11px;font-size:15px;font-weight:500;color:#222;transform:translateX(-50%)}

/* hero */
.hero{top:169px;left:0;width:1200px;height:580px;background:linear-gradient(180deg,#f4efe6 0%,#e9e1d2 40%,#d8cab3 70%,#cdbda3 100%)}
.hero-title{top:345px;font-size:52px;font-weight:700;line-height:62px;color:#111}
.hero-curve{top:640px;left:0}
.mouse{top:628px;left:582px}

/* specialties */
.intro{top:820px;font-size:34px;font-weight:300;line-height:42px;color:#222}
.wave{top:918px;left:570px}
.eyebrow{font-size:14px;font-weight:600;letter-spacing:.5px;color:#222}
.hex{width:250px;height:236px}
.hex-frame{width:100%;height:100%;background:var(--gold);clip-path:polygon(25% 0,75% 0,100% 50%,75% 100%,25% 100%,0 50%)}
.hex-photo{position:absolute;inset:8px;clip-path:polygon(25% 0,75% 0,100% 50%,75% 100%,25% 100%,0 50%)}
.specialty-label{width:260px;text-align:center;font-size:17px;line-height:29px;color:#222}
.btn{display:block;text-align:center;background:var(--cream);border:2px solid var(--gold);border-radius:30px;font-weight:600;color:#222}
.btn-view{top:1744px;left:529px;width:142px;height:42px;line-height:38px;font-size:15px}

/* features */
.features{top:1840px;left:0}
.feat-title{top:2018px;font-size:33px;font-weight:300;color:#222}
.faint{font-size:12px;color:#b8d9d3;letter-spacing:1px}
.feat-circle{width:164px;height:164px;border-radius:50%;background:var(--white);border:3px solid var(--gold);display:flex;align-items:center;justify-content:center}
.feat-name{width:260px;text-align:center;font-size:17px;font-weight:700;color:#222}
.feat-text{width:200px;text-align:center;font-size:15px;line-height:25px;color:#555}
.dots span{display:inline-block;width:9px;height:9px;border-radius:50%;background:#9bbdb8;margin:0 5px}
.dots span.on{background:#555}

/* pricing */
.pricing-photo{top:2548px;left:0}
.price-title{top:2762px;font-size:33px;font-weight:300;color:#222}
.price-card{top:2902px;left:264px;width:671px;height:300px;background:var(--white);border-radius:22px;box-shadow:0 8px 30px rgba(0,0,0,.12);text-align:center}
.price-card h3{margin-top:44px;font-size:19px;font-weight:600;color:#222}
.price-card ul{list-style:none;margin-top:30px}
.price-card li{font-size:15px;line-height:31px;color:#444}
.btn-more{top:3176px;left:460px;width:280px;height:52px;line-height:48px;font-size:18px}

/* footer */
.footer-rule{top:3306px;left:98px;width:1004px;height:1px;background:var(--line)}
.foot-h{font-size:20px;font-weight:500;color:#222}
.foot-list{font-size:14px;line-height:25.5px;color:#555;list-style:none}
.news-input{top:3453px;left:830px;width:268px;height:36px;border:1px solid var(--line);border-radius:20px;background:var(--white)}
.news-input span{position:absolute;left:16px;top:10px;font-size:12px;color:#888}
.news-input b{position:absolute;right:2px;top:2px;height:30px;width:104px;background:var(--cream);border-radius:16px;font-size:12px;line-height:30px;text-align:center;font-weight:700}
.social span{display:inline-block;width:14px;height:14px;border-radius:50%;background:#888;margin-right:20px}
.hours{top:3590px;font-size:13px;color:#444}
.bottom-bar{top:3625px;left:0;width:1200px;height:48px;background:var(--dark);color:#ddd;font-size:12px;line-height:48px;text-align:center}
</style>
</head>
<body>

<header>
  <div class="abs brand">
    <div class="brand-mark"></div>
    <div class="brand-name">LARKFIELD</div>
    <div class="brand-tag">INFECTIOUS DISEASE SPECIALISTS</div>
  </div>
  <nav class="abs main-nav">
    <a href="#" style="left:233px">HOME</a>
    <a href="#" style="left:360px">SPECIALTIES</a>
    <a href="#" style="left:500px">PRICING</a>
    <a href="#" style="left:629px">ABOUT US</a>
    <a href="#" style="left:747px">FAQ</a>
    <a href="#" style="left:845px">BLOG</a>
    <a href="#" style="left:958px">JOIN US</a>
  </nav>
</header>

<section>
  <div class="abs hero" role="img" aria-label="Group of friends standing on a sunny beach, seen from behind"></div>
  <svg class="abs hero-curve" width="1200" height="120" viewBox="0 0 1200 120"><path d="M0 120 L0 95 Q600 0 1200 95 L1200 120 Z" fill="#ffffff"/></svg>
  <h1 class="abs center hero-title">Specialty medicine with<br>Commitment, Compassion and Care</h1>
  <svg class="abs mouse" width="36" height="80" viewBox="0 0 36 80"><rect x="4" y="2" width="28" height="46" rx="14" fill="#fff" stroke="#222" stroke-width="2.5"/><line x1="18" y1="12" x2="18" y2="22" stroke="#222" stroke-width="2.5"/><line x1="18" y1="54" x2="18" y2="74" stroke="#222" stroke-width="2.5"/><path d="M11 67 L18 75 L25 67" fill="none" stroke="#222" stroke-width="2.5"/></svg>
</section>

<section>
  <h2 class="abs center intro">We offer comprehensive treatment of a wide<br>variety of infectious diseases.</h2>
  <svg class="abs wave" width="60" height="20" viewBox="0 0 60 20"><path d="M0 4 q7.5 -4 15 0 t15 0 t15 0 t15 0 M0 10 q7.5 -4 15 0 t15 0 t15 0 t15 0 M0 16 q7.5 -4 15 0 t15 0 t15 0 t15 0" fill="none" stroke="#999" stroke-width="1.4"/></svg>
  <p class="abs center eyebrow" style="top:957px">OUT EXPERTISE IS IN THE FOLLOWING AREA.</p>

  <div class="abs hex" style="left:164px;top:1021px"><div class="hex-frame"></div><div class="hex-photo" role="img" aria-label="Person in a yellow jacket looking over a valley" style="background:linear-gradient(160deg,#b9d3d9,#7f9c86 60%,#6d6b47)"></div></div>
  <div class="abs hex" style="left:475px;top:1021px"><div class="hex-frame"></div><div class="hex-photo" role="img" aria-label="Person leaping across an open field" style="background:linear-gradient(180deg,#a9c2c6,#8aa7a3 55%,#5e5a3f)"></div></div>
  <div class="abs hex" style="left:786px;top:1021px"><div class="hex-frame"></div><div class="hex-photo" role="img" aria-label="Smiling couple relaxing together at home" style="background:linear-gradient(150deg,#e8ddd2,#c9a489 60%,#8c6a55)"></div></div>

  <p class="abs specialty-label" style="left:159px;top:1272px">HIV/PREP</p>
  <p class="abs specialty-label" style="left:470px;top:1272px">CHRONIC HEPATITIS</p>
  <p class="abs specialty-label" style="left:781px;top:1272px">SEXUALLY TRANSMITTED<br>INFECTIONS</p>

  <div class="abs hex" style="left:164px;top:1389px"><div class="hex-frame"></div><div class="hex-photo" role="img" aria-label="Enamel travel mug held in hands" style="background:linear-gradient(160deg,#b5303a,#7d1f27 55%,#3a2422)"></div></div>
  <div class="abs hex" style="left:475px;top:1389px"><div class="hex-frame"></div><div class="hex-photo" role="img" aria-label="Woman outdoors among green foliage" style="background:linear-gradient(160deg,#cde07a,#7ea83a 55%,#3f5e20)"></div></div>
  <div class="abs hex" style="left:786px;top:1389px"><div class="hex-frame"></div><div class="hex-photo" role="img" aria-label="Two hikers on a mountain ridge" style="background:linear-gradient(180deg,#8cc3e8,#5f93c4 55%,#2f4e72)"></div></div>

  <p class="abs specialty-label" style="left:159px;top:1642px">PRE-TRAVEL VACCINATIONS<br>AND COUNSELLING</p>
  <p class="abs specialty-label" style="left:470px;top:1642px">DIABETES RELATED<br>INFECTIONS</p>
  <p class="abs specialty-label" style="left:781px;top:1642px">POSTSURGICAL INFECTIONS</p>

  <a class="abs btn btn-view" href="#">View All</a>
</section>

<section>
  <svg class="abs features" width="1200" height="880" viewBox="0 0 1200 880"><path d="M0 10 Q600 120 1200 10 L1200 880 L0 880 Z" fill="#cfeae6"/></svg>
  <h2 class="abs center feat-title">Less wait, more personal.</h2>
  <p class="abs center faint" style="top:2069px">Our promise</p>
  <p class="abs center eyebrow" style="top:2107px">WE ARE NOT YOUR TRADITIONAL DOCTOR'S OFFICE.</p>

  <div class="abs feat-circle" style="left:129px;top:2167px"><svg width="76" height="76" viewBox="0 0 76 76" fill="none" stroke="#666" stroke-width="3"><circle cx="42" cy="22" r="15"/><path d="M42 13v18M47 16h-7a3 3 0 0 0 0 6h4a3 3 0 0 1 0 6h-7"/><path d="M8 52l12-8h14a4 4 0 0 1 0 8h-10M34 52l20-10a4 4 0 0 1 4 7l-22 14H8"/></svg></div>
  <div class="abs feat-circle" style="left:388px;top:2167px"><svg width="76" height="76" viewBox="0 0 76 76" fill="none" stroke="#666" stroke-width="3"><circle cx="38" cy="42" r="24"/><path d="M38 28v15l10 7M12 18l10-8M64 18l-10-8M20 66l-4 6M56 66l4 6"/></svg></div>
  <div class="abs feat-circle" style="left:648px;top:2167px"><svg width="76" height="76" viewBox="0 0 76 76" fill="none" stroke="#666" stroke-width="3"><path d="M40 34S26 25 26 17a7 7 0 0 1 14-2 7 7 0 0 1 14 2c0 8-14 17-14 17z"/><path d="M8 56l12-8h14a4 4 0 0 1 0 8h-10M34 56l20-10a4 4 0 0 1 4 7l-22 14H8"/></svg></div>
  <div class="abs feat-circle" style="left:907px;top:2167px"><svg width="76" height="76" viewBox="0 0 76 76" fill="none" stroke="#666" stroke-width="3"><rect x="8" y="22" width="44" height="34" rx="5"/><circle cx="30" cy="39" r="9"/><path d="M52 34l16-9v28l-16-9z"/></svg></div>

  <p class="abs feat-name" style="left:81px;top:2344px">Straightforward pricing</p>
  <p class="abs feat-name" style="left:340px;top:2344px">Available when you are</p>
  <p class="abs feat-name" style="left:600px;top:2344px">Devoted care</p>
  <p class="abs feat-name" style="left:859px;top:2344px">Within your reach</p>

  <p class="abs feat-text" style="left:111px;top:2384px">We charge all our patients the same low rate - no surprises.</p>
  <p class="abs feat-text" style="left:370px;top:2384px">New patient appointments are available within 1 week.</p>
  <p class="abs feat-text" style="left:630px;top:2384px">We schedule enough time at each visit to make sure all of your questions are</p>
  <p class="abs feat-text" style="left:889px;top:2384px">Follow-up appointments may be done by video chat for your convenience.</p>

  <div class="abs center dots" style="top:2488px"><span class="on"></span><span></span><span></span></div>
</section>

<section>
  <svg class="abs pricing-photo" width="1200" height="558" viewBox="0 0 1200 558" role="img" aria-label="Misty green hillside meadow with grazing sheep">
    <defs>
      <linearGradient id="meadow" x1="0" y1="0" x2="0" y2="1">
        <stop offset="0" stop-color="#dfe1e4"/>
        <stop offset="0.4" stop-color="#c9cccf"/>
        <stop offset="0.65" stop-color="#8d9788"/>
        <stop offset="0.85" stop-color="#596b50"/>
        <stop offset="1" stop-color="#4e5f45"/>
      </linearGradient>
    </defs>
    <path d="M0 134 Q600 0 1200 134 L1200 558 L0 558 Z" fill="url(#meadow)"/>
  </svg>
  <h2 class="abs center price-title">Our pricing is simple, transparent and affordable.</h2>
  <p class="abs center faint" style="top:2816px;color:#aeb3b5">Simple plans</p>
  <div class="abs price-card">
    <h3>Membership Plan $80/mo, plus a one-time $99 enrollment fee.</h3>
    <ul>
      <li>Includes all appointments, no co-pay</li>
      <li>Relaxed, unrushed visits</li>
      <li>Direct communication with your doctor via phone, email, video chat 24/7</li>
      <li>Convenient online scheduling (no need to call during business hours)</li>
      <li>Wholesale price for labs and medications</li>
    </ul>
  </div>
  <a class="abs btn btn-more" href="#">Learn more about us</a>
</section>

<footer>
  <div class="abs footer-rule"></div>
  <h4 class="abs foot-h" style="left:98px;top:3368px">Links</h4>
  <ul class="abs foot-list" style="left:98px;top:3411px"><li>Home</li><li>Specialties</li><li>Pricing</li><li>About Us</li><li>Faq</li></ul>
  <ul class="abs foot-list" style="left:289px;top:3411px"><li>Blog</li><li>Join Us</li></ul>

  <h4 class="abs foot-h" style="left:490px;top:3368px">Contact Us</h4>
  <ul class="abs foot-list" style="left:490px;top:3411px;line-height:30px"><li>24 Alder Row, Fenmouth,</li><li>Fenmouth FN4 2QT</li><li>Phone: 020 7946 0321</li><li>Email: info@larkfieldid.com</li></ul>

  <h4 class="abs foot-h" style="left:830px;top:3368px">Newsletter</h4>
  <p class="abs foot-list" style="left:830px;top:3408px">Subscribe Our Newsletter For More Info</p>
  <div class="abs news-input"><span>Email Address</span><b>SUBSCRIBE</b></div>
  <div class="abs social" style="left:830px;top:3537px"><span></span><span></span><span></span><span></span><span></span></div>

  <p class="abs center hours">Opening Hours : Monday – Friday, 8:00 a.m. – 5:00 p.m.</p>
  <div class="abs bottom-bar">© 2019 Copyrights.The Company Name.All Rights Reserved</div>
</footer>

</body>
</html>
```